Government contracting small business needs a web design

Tarvex Summit Inc is a veteran owned small business that delivers a full range of professional services as well as training in information technology, security and defense intelligence solutions.
We need a professional/corporate looking website where potential clients can view what services are offered.
This being a new company, there is not much that can added more than a narrative statement, stock photos and a place where potential customers and employees can make contact.
Open to ideas.
Target Market(s)
US Government
Industry/Entity Type
Small Business
Look and feel
Each slider illustrates characteristics of the customer's brand and the style your logo design should communicate.

```html
<!DOCTYPE html>
<html lang="en">
<head>
<meta charset="utf-8">
<title>Tarvex Summit Inc</title>
<link href="https://fonts.googleapis.com/css2?family=Arimo:wght@400;700&family=Noto+Sans:ital,wght@0,400;1,400&display=swap" rel="stylesheet">
<style>
:root{
  --blue:#1a7fc0;
  --tab-blue:#1384cc;
  --ink:#333;
  --muted:#555;
  --header-bg:#ececec;
  --body-bg:#f3f4f5;
  --tech-bg:#e9ebee;
  --line:#cfd2d5;
  --tech-title:#b0650a;
  --panel-blue:#74b8de;
  --panel-gray:#8197a7;
}
*{box-sizing:border-box;margin:0;padding:0}
html,body{width:885px;height:1200px;overflow:hidden;background:#fff}
body{position:relative;font-family:"Noto Sans",Verdana,sans-serif;color:var(--ink)}
.abs{position:absolute}
a{color:var(--blue);text-decoration:none}
.more{font-style:italic;color:var(--blue);white-space:nowrap}

.site-header{left:0;top:0;width:885px;height:93px;background:var(--header-bg)}
.brand{left:35px;top:12px;display:flex;align-items:center;gap:8px}
.brand-mark{width:62px;height:56px;border-radius:50%;background:#6c6c6c}
.brand-name{font-family:Arimo,Arial,sans-serif;font-weight:700;font-size:32px;color:#5a5a5a}
.util-links{right:22px;top:68px;font-family:Arimo,Arial,sans-serif;font-size:12.5px;color:var(--blue)}

.main-nav{left:0;top:93px;width:885px;height:62px;background:linear-gradient(#fafafa,#e6e6e6 45%,#dedede 55%,#efefef);border-top:1px solid #d6d6d6;border-bottom:1px solid #d6d6d6}
.nav-item{position:absolute;top:0;height:60px;line-height:60px;text-align:center;font-family:Arimo,Arial,sans-serif;font-size:11px;color:#444;border-left:1px solid #cfcfcf;white-space:nowrap}
.nav-item.current{color:var(--blue);background:linear-gradient(#fff,#eee)}
.nav-end{position:absolute;left:547px;top:0;height:60px;border-left:1px solid #cfcfcf}
.search{left:592px;top:14px;width:234px;height:34px;border-radius:17px;background:#fff;border:1px solid #d0d0d0;font-size:11px;font-style:italic;color:#555;padding:9px 14px}
.search-go{left:830px;top:14px;width:48px;height:34px;border-radius:17px;background:linear-gradient(#fff,#e4e4e4);border:1px solid #d0d0d0;font-size:11px;text-align:center;line-height:32px;color:#444}

.hero{left:17px;top:171px;width:847px;height:242px;background:#fff}
.hero-visual{left:8px;top:7px;width:544px;height:227px;background:radial-gradient(ellipse at 50% 45%,#a84a1c 0,#d58a44 35%,#f2e4cc 75%)}
.hero-panel{left:564px;width:273px;height:70px;padding:5px 6px;color:#fff}
.hero-panel h3{font-family:Arimo,Arial,sans-serif;font-weight:400;font-size:17px;line-height:20px}
.hero-panel p{font-size:10.2px;line-height:14px;color:#2a2a2a;margin-top:2px;letter-spacing:-0.1px}
.hero-panel.active{background:linear-gradient(#86c6e8,var(--panel-blue))}
.hero-panel.idle{background:linear-gradient(#a3b4c0,var(--panel-gray))}

.content{left:0;top:428px;width:885px;height:625px;background:var(--body-bg);border-top:1px solid #e3e3e3}
.welcome{left:37px;top:20px;width:816px}
.welcome h1{font-family:Arimo,Arial,sans-serif;font-weight:400;font-size:17px;color:var(--blue);margin-bottom:12px}
.welcome p{font-size:10.6px;line-height:14.2px;text-align:justify;margin-bottom:15px;padding-left:2px}

.tech{left:13px;top:186px;width:858px;height:242px;background:var(--tech-bg)}
.tech-tab{left:9px;top:-12px;width:210px;height:44px;background:var(--tab-blue);color:#fff;font-family:Arimo,Arial,sans-serif;font-weight:400;font-size:19px;line-height:24px;padding:10px 26px;white-space:nowrap}
.tech-fold{left:219px;top:-12px;width:0;height:0;border-left:11px solid #0b5c8f;border-top:11px solid transparent}
.tech-item{width:400px}
.tech-icon{position:absolute;left:0;top:0;width:70px;height:72px;border-radius:50%;background:radial-gradient(circle at 55% 40%,#bfe3ef,#4a9fc0 60%,#d99a2a)}
.tech-item h4{position:absolute;left:85px;top:0;font-family:Arimo,Arial,sans-serif;font-weight:400;font-size:14px;color:var(--tech-title)}
.tech-item p{position:absolute;left:86px;top:25px;width:305px;font-size:10.4px;line-height:13.3px;text-align:justify}

.card{top:475px;width:256px;height:129px;border:1px solid var(--line);border-radius:16px;background:linear-gradient(#f9f9f9,#eef0f1)}
.card h2{position:absolute;left:23px;top:4px;font-family:Arimo,Arial,sans-serif;font-weight:400;font-size:19px;color:var(--blue)}
.card p{position:absolute;left:26px;top:35px;width:194px;font-size:10.1px;line-height:16px;text-align:justify;color:#444;hyphens:auto;-webkit-hyphens:auto}
.card-art{position:absolute;top:-40px;width:56px;height:64px}

.site-footer{left:60px;top:1081px;width:767px;height:78px;border:1px solid #cfcfcf;border-radius:30px;background:#f1f1f1}
.copyright{left:20px;top:32px;font-size:8.5px;color:#444}
.footer-nav{right:32px;top:33px;font-family:Arimo,Arial,sans-serif;font-size:11px;color:#555;display:flex;gap:18px;white-space:nowrap}
</style>
</head>
<body>

<header class="site-header abs">
  <div class="brand abs"><span class="brand-mark"></span><span class="brand-name">Tarvex Summit</span></div>
  <nav class="util-links abs"><a href="#">Sign in</a> | <a href="#">Sign Up</a> | <a href="#">Site Map</a></nav>
</header>

<nav class="main-nav abs">
  <a class="nav-item current" style="left:60px;width:68px" href="#">HOME</a>
  <a class="nav-item" style="left:128px;width:89px" href="#">SERVICES</a>
  <a class="nav-item" style="left:217px;width:93px" href="#">SOLUTIONS</a>
  <a class="nav-item" style="left:310px;width:77px" href="#">ABOUT &nbsp;US</a>
  <a class="nav-item" style="left:387px;width:97px" href="#">CONTACT US</a>
  <a class="nav-item" style="left:484px;width:63px;text-align:left;padding-left:9px" href="#">LOGIN</a>
  <span class="nav-end"></span>
  <div class="search abs">Search...</div>
  <div class="search-go abs">Go!</div>
</nav>

<section class="hero abs">
  <div class="hero-visual abs" role="img" aria-label="Circuit board with a padlock chip in warm copper tones"></div>
  <div class="hero-panel active abs" style="top:9px"><h3>Lorem ipsum dolor sit</h3><p>Lorem ipsum dolor sit amet, consectetur adipiscing elit. &nbsp;<span class="more" style="color:#2a2a2a">Read More...</span></p></div>
  <div class="hero-panel idle abs" style="top:86px"><h3>Lorem ipsum dolor sit</h3><p>Lorem ipsum dolor sit amet, consectetur adipiscing elit. &nbsp;<span class="more" style="color:#2a2a2a">Read More...</span></p></div>
  <div class="hero-panel idle abs" style="top:162px"><h3>Lorem ipsum dolor sit</h3><p>Lorem ipsum dolor sit amet, consectetur adipiscing elit. &nbsp;<span class="more" style="color:#2a2a2a">Read More...</span></p></div>
</section>

<main class="content abs">
  <section class="welcome abs">
    <h1>Welcome to Our Website...</h1>
    <p>Lorem ipsum dolor sit amet, consectetur adipiscing elit. Maecenas feugiat mattis nulla, a consequat diam commodo tincidunt. Mauris suscipit porta ornare. Pellentesque turpis metus, vestibulum vitae dictum eu, vulputate vel neque. Lorem ipsum dolor sit amet, consectetur adipiscing elit. Maecenas feugiat mattis nulla, a consequat diam commodo tincidunt. Mauris suscipit porta ornare. Pellentesque turpis metus, vestibulum vitae dictum eu, vulputate vel neque. <a href="#">Lorem ipsum dolor sit amet, consectetur adipiscing elit. Maecenas feugiat mattis nulla</a>, a consequat diam commodo tincidunt. Mauris suscipit porta ornare.</p>
    <p>Pellentesque turpis metus, vestibulum vitae dictum eu, vulputate vel neque. Lorem ipsum dolor sit amet, consectetur adipiscing elit. Maecenas feugiat mattis nulla, a consequat diam commodo tincidunt. Mauris suscipit porta ornare. Pellentesque turpis metus, vestibulum vitae dictum eu. &nbsp;<span class="more">Read More...</span></p>
  </section>

  <section class="tech abs">
    <h2 class="tech-tab abs">Our Technologies</h2>
    <span class="tech-fold abs"></span>
    <div class="tech-item abs" style="left:22px;top:48px"><span class="tech-icon" role="img" aria-label="Globe and compass icon"></span><h4>Technology 1</h4><p>Lorem ipsum dolor sit amet, consectetur adipiscing elit. Maecenas feugiat mattis nulla, a consequat diam commodo tincidunt. Pellentesque turpis metus. <span class="more">Read More...</span></p></div>
    <div class="tech-item abs" style="left:443px;top:48px"><span class="tech-icon" role="img" aria-label="Globe and compass icon"></span><h4>Technology 3</h4><p>Lorem ipsum dolor sit amet, consectetur adipiscing elit. Maecenas feugiat mattis nulla, a consequat diam commodo tincidunt. Pellentesque turpis metus. <span class="more">Read More...</span></p></div>
    <div class="tech-item abs" style="left:22px;top:154px"><span class="tech-icon" role="img" aria-label="Globe and compass icon"></span><h4>Technology 2</h4><p>Lorem ipsum dolor sit amet, consectetur adipiscing elit. Maecenas feugiat mattis nulla, a consequat diam commodo tincidunt. Pellentesque turpis metus. <span class="more">Read More...</span></p></div>
    <div class="tech-item abs" style="left:443px;top:154px"><span class="tech-icon" role="img" aria-label="Globe and compass icon"></span><h4>Technology 4</h4><p>Lorem ipsum dolor sit amet, consectetur adipiscing elit. Maecenas feugiat mattis nulla, a consequat diam commodo tincidunt. Pellentesque turpis metus. <span class="more">Read More...</span></p></div>
  </section>

  <article class="card abs" style="left:8px">
    <span class="card-art" style="left:210px;background:linear-gradient(#c98a5a,#3b6ea8)" role="img" aria-label="Job seeker badge icon"></span>
    <h2>Careers</h2>
    <p>Lorem ipsum dolor sit amet, consectetur adipiscing elit. Maecenas feugiat mattis nulla, a consequat diam commodo tincidunt. Pellentesque turpis metus. <span class="more">Read More...</span></p>
  </article>
  <article class="card abs" style="left:294px">
    <span class="card-art" style="left:214px;background:linear-gradient(#fafafa,#d8d8d8)" role="img" aria-label="Report document with line chart icon"></span>
    <h2 style="left:25px">News &amp; Events</h2>
    <p>Lorem ipsum dolor sit amet, consectetur adipiscing elit. Maecenas feugiat mattis nulla, a consequat diam commodo tincidunt. Pellentesque turpis metus. <span class="more">Read More...</span></p>
  </article>
  <article class="card abs" style="left:588px">
    <span class="card-art" style="left:214px;background:linear-gradient(#d2312b,#8e1a16)" role="img" aria-label="Red portfolio binder icon"></span>
    <h2 style="left:25px">Our Customers</h2>
    <p>Lorem ipsum dolor sit amet, consectetur adipiscing elit. Maecenas feugiat mattis nulla, a consequat diam commodo tincidunt. Pellentesque turpis metus. <span class="more">Read More...</span></p>
  </article>
</main>

<footer class="site-footer abs">
  <p class="copyright abs">Copyright 2012 &nbsp;yoursite.com | All Rights Reserved</p>
  <nav class="footer-nav abs"><span>HOME</span><span>SERVICES</span><span>SOLUTIONS</span><span>ABOUT &nbsp;US</span><span>CONTACT US</span></nav>
</footer>

</body>
</html>
```